Banner Ad Design Project

I require banner ad designs with the below wording.

1. Join Today and Make Money Tomorrow. Unlimited Income. Click Here Now

2. I lost my job. Now I Make Over $5,000 Per Week From Home. You Can Too. Free Info, Apply Now

I require sizes: 300x250 and 728x90 and 468x60 and 120x240

The design should communicate legitimate, accredited, online business.

Industry/Entity Type

Business

Requirements
Should not have
• Creative attributes to avoid*
Phone numbers in creative
Creative with no click buttons
Interactive creative
Brand messaging with no call to action
Creative with long looping times

```html
<!DOCTYPE html>
<html lang="en">
<head>
<meta charset="utf-8">
<title>Work From Home Banner Set</title>
<link href="https://fonts.googleapis.com/css2?family=Roboto+Condensed:wght@400;500;700&family=Delius&display=swap" rel="stylesheet">
<style>
  :root {
    --stage-top: #020202;
    --stage-bottom: #474747;
    --crimson: #cf1655;
    --crimson-deep: #a50d3f;
    --crimson-edge: #e2547f;
    --gold-light: #fff65e;
    --gold-deep: #f2c200;
    --white: #ffffff;
    --button-top: #ffffff;
    --button-bottom: #d9d9d9;
    --photo-light: #f6f3f0;
    --photo-mid: #d8cfc8;
  }
  * { margin: 0; padding: 0; box-sizing: border-box; }
  html, body { width: 1200px; height: 848px; overflow: hidden; }
  body {
    position: relative;
    background: linear-gradient(180deg, var(--stage-top) 0%, var(--stage-bottom) 100%);
    font-family: "Roboto Condensed", "Arial Narrow", sans-serif;
  }
  .banner {
    position: absolute;
    overflow: hidden;
    background: radial-gradient(ellipse at 55% 45%, var(--crimson) 45%, var(--crimson-deep) 100%);
    color: var(--white);
  }
  .banner--rectangle  { left: 292px; top: 79px;  width: 390px; height: 324px; }
  .banner--skyscraper { left: 738px; top: 79px;  width: 156px; height: 311px; }
  .banner--leaderboard{ left: 177px; top: 484px; width: 945px; height: 117px; }
  .banner--fullsize   { left: 345px; top: 657px; width: 608px; height: 78px; }

  .photo { position: absolute; left: 0; top: 0; }
  .text-block { position: absolute; top: 0; }
  .line {
    position: absolute;
    left: 0; right: 0;
    text-align: center;
    white-space: nowrap;
    line-height: 1;
    text-shadow: 0 1px 2px rgba(90, 0, 30, 0.45);
  }
  .line--lead { font-weight: 500; }
  .line--amount {
    font-weight: 700;
    background: linear-gradient(180deg, var(--gold-light) 20%, var(--gold-deep) 90%);
    -webkit-background-clip: text;
    background-clip: text;
    color: transparent;
    text-shadow: none;
    filter: drop-shadow(0 1px 1px rgba(90, 0, 30, 0.6));
  }
  .line--place { font-weight: 500; }
  .line--invite { font-family: "Delius", "Comic Neue", cursive; letter-spacing: -0.3px; }
  .apply-button {
    position: absolute;
    display: flex;
    align-items: center;
    justify-content: center;
    border-radius: 999px;
    background: linear-gradient(180deg, var(--button-top) 40%, var(--button-bottom) 100%);
    box-shadow: 0 1px 3px rgba(60, 0, 20, 0.5);
    color: var(--crimson);
    font-weight: 500;
    white-space: nowrap;
  }
  .top-strip {
    position: absolute;
    left: 635px; top: 0;
    width: 288px; height: 8px;
    background: var(--white);
    border-radius: 0 0 4px 4px;
  }
</style>
</head>
<body>

<section class="banner banner--rectangle">
  <svg class="photo" width="390" height="324" viewBox="0 0 390 324" role="img" aria-label="Photo of a cheering businesswoman in a suit with arms raised">
    <defs>
      <linearGradient id="photo-fill-a" x1="0" y1="0" x2="1" y2="1">
        <stop offset="0" stop-color="var(--photo-light)"/>
        <stop offset="1" stop-color="var(--photo-mid)"/>
      </linearGradient>
    </defs>
    <path d="M48,0 C62,70 140,118 240,124 L390,130 L390,0 Z" fill="url(#photo-fill-a)"/>
    <path d="M48,0 C62,70 140,118 240,124 L390,130" fill="none" stroke="var(--crimson-edge)" stroke-width="3"/>
  </svg>
  <p class="line line--lead"   style="top:143px; font-size:23px;">I lost my job Now I Make Over</p>
  <p class="line line--amount" style="top:173px; font-size:36px;">$5,000 Per Week</p>
  <p class="line line--place"  style="top:213px; font-size:23px;">From Home</p>
  <p class="line line--invite" style="top:245px; font-size:34px;">You Can Too Free Info</p>
  <a class="apply-button" style="left:110px; top:286px; width:169px; height:34px; font-size:20px;">Apply Now</a>
</section>

<section class="banner banner--skyscraper">
  <svg class="photo" width="156" height="311" viewBox="0 0 156 311" role="img" aria-label="Photo of a cheering businesswoman in a suit with arms raised">
    <defs>
      <linearGradient id="photo-fill-b" x1="0" y1="0" x2="1" y2="1">
        <stop offset="0" stop-color="var(--photo-light)"/>
        <stop offset="1" stop-color="var(--photo-mid)"/>
      </linearGradient>
    </defs>
    <path d="M0,0 H156 V110 C110,108 40,96 0,80 Z" fill="url(#photo-fill-b)"/>
    <path d="M156,110 C110,108 40,96 0,80" fill="none" stroke="var(--crimson-edge)" stroke-width="2.5"/>
  </svg>
  <p class="line line--lead"   style="top:124px; font-size:19px;">I lost my job</p>
  <p class="line line--lead"   style="top:153px; font-size:19px;">Now I Make Over</p>
  <p class="line line--amount" style="top:181px; font-size:29px;">$5,000</p>
  <p class="line line--amount" style="top:213px; font-size:29px;">Per Week</p>
  <p class="line line--place"  style="top:246px; font-size:18px;">From Home</p>
  <a class="apply-button" style="left:17px; top:272px; width:125px; height:29px; font-size:16px;">Apply Now</a>
</section>

<section class="banner banner--leaderboard">
  <svg class="photo" width="240" height="117" viewBox="0 0 240 117" role="img" aria-label="Photo of a cheering businesswoman in a suit with arms raised">
    <defs>
      <linearGradient id="photo-fill-c" x1="0" y1="0" x2="1" y2="1">
        <stop offset="0" stop-color="var(--photo-light)"/>
        <stop offset="1" stop-color="var(--photo-mid)"/>
      </linearGradient>
    </defs>
    <path d="M0,0 H208 C186,35 180,85 214,117 H0 Z" fill="url(#photo-fill-c)"/>
    <path d="M208,0 C186,35 180,85 214,117" fill="none" stroke="var(--crimson-edge)" stroke-width="3"/>
  </svg>
  <div class="top-strip"></div>
  <div class="text-block" style="left:244px; width:310px; height:117px;">
    <p class="line line--lead"   style="top:13px; font-size:26px;">I lost my job Now I Make Over</p>
    <p class="line line--amount" style="top:43px; font-size:38px;">$5,000 Per Week</p>
    <p class="line line--place"  style="top:83px; font-size:24px;">From Home</p>
  </div>
  <div class="text-block" style="left:624px; width:310px; height:117px;">
    <p class="line line--invite" style="top:29px; font-size:29px;">You Can Too Free Info</p>
  </div>
  <a class="apply-button" style="left:688px; top:71px; width:182px; height:34px; font-size:21px;">Apply Now</a>
</section>

<section class="banner banner--fullsize">
  <svg class="photo" width="160" height="78" viewBox="0 0 160 78" role="img" aria-label="Photo of a cheering businesswoman in a suit with arms raised">
    <defs>
      <linearGradient id="photo-fill-d" x1="0" y1="0" x2="1" y2="1">
        <stop offset="0" stop-color="var(--photo-light)"/>
        <stop offset="1" stop-color="var(--photo-mid)"/>
      </linearGradient>
    </defs>
    <path d="M0,0 H146 C128,22 124,55 146,78 H0 Z" fill="url(#photo-fill-d)"/>
    <path d="M146,0 C128,22 124,55 146,78" fill="none" stroke="var(--crimson-edge)" stroke-width="2.5"/>
  </svg>
  <div class="text-block" style="left:152px; width:220px; height:78px;">
    <p class="line line--lead"   style="top:9px;  font-size:17px;">I lost my job Now I Make Over</p>
    <p class="line line--amount" style="top:27px; font-size:25px;">$5,000 Per Week</p>
    <p class="line line--place"  style="top:57px; font-size:15px;">From Home</p>
  </div>
  <div class="text-block" style="left:390px; width:210px; height:78px;">
    <p class="line line--invite" style="top:17px; font-size:19px;">You Can Too Free Info</p>
  </div>
  <a class="apply-button" style="left:434px; top:47px; width:123px; height:22px; font-size:14px;">Apply Now</a>
</section>

</body>
</html>
```